NEW Modern Sleek Business Card for VR Language Startup

Our startup is using VR to lead the next wave of world language education. We need a two-sided business card that introduces the larger organization (Lumivessa Language Inc) and our contact info on one side and shows the product, Glimwoorld, on the other side.

Side 1 (contact info)= Lumivessa Logo and Contact info (name, title, phone, email)

Side 2 (product)= Glimworld logo, text, and website
Text= Culturally Immersive Language Learning Games
Website= www.glimworld-play.com

Target Market(s)

Education, Technology

Contact Information for Business Card

Contact info will be updated upon approval of the design. For now, put this as a placeholder.

Perry Dunmore
Founder & CEO
pdunmore@quillpost-mail.net
(555)-014-2286

Font styles to use
Other font styles liked:
• Gibson and Century Gothic are the brand fonts

Requirements
Nice to have
• I would love to see cohesion between the design and colors of the two logos. I have attached a few business card designs that I like, so you can get a feel for my preferred style.

```html
<!DOCTYPE html>
<html lang="en">
<head>
<meta charset="utf-8">
<title>Lumivessa Language — Business Card</title>
<link rel="stylesheet" href="https://fonts.googleapis.com/css2?family=Montserrat:wght@400;600;700&family=Questrial&display=swap">
<style>
  :root {
    --stage: #3b3c3f;
    --card-white: #ffffff;
    --ice-light: #e6f6fd;
    --ice-mid: #b4e4f8;
    --ice-deep: #5cc8f0;
    --ink: #1b1b1d;
    --accent: #f0563a;
    --teal-text: #1f9fc4;
    --violet: #5a58a4;
    --sky: #5fc6d9;
    --tagline: #3d4f9a;
    --white: #ffffff;
  }
  * { box-sizing: border-box; margin: 0; padding: 0; }
  html, body {
    width: 1200px; height: 900px; overflow: hidden;
    background: var(--stage);
  }
  .stage {
    position: relative; width: 1200px; height: 900px;
    display: flex; flex-direction: column; align-items: center; justify-content: center;
    gap: 40px;
  }
  .card {
    position: relative; width: 700px; height: 400px;
    border-radius: 28px; overflow: hidden;
  }

  /* Contact side */
  .card--contact { background: var(--card-white); }
  .contact__facets {
    position: absolute; inset: 0;
    background: linear-gradient(115deg, var(--card-white) 0%, var(--card-white) 30%, var(--ice-light) 48%, var(--ice-mid) 75%, var(--ice-deep) 100%);
  }
  .brand {
    position: absolute; left: 60px; top: 172px;
    display: flex; align-items: center; gap: 18px;
  }
  .brand__dot {
    width: 52px; height: 52px; border-radius: 50%;
    background: var(--accent);
  }
  .brand__name {
    font-family: "Montserrat", sans-serif; font-weight: 700;
    font-size: 44px; letter-spacing: 4px; color: var(--ink); text-transform: uppercase;
  }
  .person {
    position: absolute; right: 60px; top: 52px; text-align: right;
    color: var(--white);
  }
  .person__name {
    font-family: "Montserrat", sans-serif; font-weight: 700; font-size: 26px; letter-spacing: 1px;
  }
  .person__title {
    font-family: "Questrial", sans-serif; font-size: 17px; letter-spacing: 2px; margin-top: 4px;
  }
  .contact-lines {
    position: absolute; right: 60px; bottom: 70px; text-align: right;
    font-family: "Questrial", sans-serif; font-size: 20px; letter-spacing: 1px;
    color: var(--teal-text); line-height: 1.4; text-transform: uppercase;
  }

  /* Product side */
  .card--product {
    background: linear-gradient(120deg, var(--violet) 0%, #5a83c4 50%, var(--sky) 100%);
    display: flex; flex-direction: column; align-items: center; justify-content: center;
    text-align: center;
  }
  .product-brand {
    display: flex; align-items: center; gap: 20px; margin-bottom: 34px;
  }
  .product-brand__dot {
    width: 64px; height: 64px; border-radius: 50%; background: var(--white);
  }
  .product-brand__name {
    font-family: "Montserrat", sans-serif; font-weight: 700; font-size: 64px; color: var(--white);
  }
  .tagline {
    font-family: "Questrial", sans-serif; font-size: 22px; letter-spacing: 1.5px;
    color: var(--tagline); text-transform: uppercase;
  }
  .website {
    font-family: "Questrial", sans-serif; font-size: 22px; letter-spacing: 2px;
    color: var(--white); text-transform: uppercase; margin-top: 8px;
  }
</style>
</head>
<body>
  <main class="stage">
    <section class="card card--contact">
      <div class="contact__facets" role="img" aria-label="Light blue faceted polygon background pattern"></div>
      <div class="brand">
        <span class="brand__dot"></span>
        <span class="brand__name">Lumivessa</span>
      </div>
      <div class="person">
        <p class="person__name">PERRY DUNMORE</p>
        <p class="person__title">FOUNDER &amp; CEO</p>
      </div>
      <div class="contact-lines">
        <p>pdunmore@quillpost-mail.net</p>
        <p>(555)-014-2286</p>
      </div>
    </section>

    <section class="card card--product">
      <div class="product-brand">
        <span class="product-brand__dot"></span>
        <span class="product-brand__name">Glimworld</span>
      </div>
      <p class="tagline">Culturally Immersive Language Learning Games</p>
      <p class="website">www.glimworld-play.com</p>
    </section>
  </main>
</body>
</html>
```